Real Estate agent needs flyer/folder to contain bio and overview of services

I'm including files of the layout of the small folder. The folder is 6 1/2 across and 9 1/2 inches long. It will have a front & back cover and then writing on the 2 inside pages.

I am sending a few files to incorporate into the flyer, 1 new logo to use and 2 files which are coloring ideas.

Colors

Designer to choose colors to be used in the design.

```html
<!DOCTYPE html>
<html lang="en">
<head>
<meta charset="utf-8">
<title>Dana Moretti – Realtor Folder</title>
<link href="https://fonts.googleapis.com/css2?family=Libre+Baskerville:ital,wght@0,400;0,700;1,400&family=Crimson+Text:ital,wght@0,400;0,600;1,400&family=Open+Sans:wght@400;600&display=swap" rel="stylesheet">
<style>
:root{
  --stage:#3d3d3f;
  --blue:#2f5aab;
  --blue-deep:#25489a;
  --blue-light:#6f8fd0;
  --paper:#ffffff;
  --paper-gray:#eceef2;
  --ink:#3a3a3a;
  --ink-soft:#555;
  --white:#fff;
}
*{margin:0;padding:0;box-sizing:border-box}
html,body{width:837px;height:1200px;overflow:hidden;background:var(--stage)}
body{position:relative;font-family:"Crimson Text",Georgia,serif;color:var(--ink)}
.spread{position:absolute;width:709px;height:530px;filter:drop-shadow(2px 3px 4px rgba(0,0,0,.45))}
.spread-outside{left:56px;top:56px}
.spread-inside{left:72px;top:614px}
.spread>svg{position:absolute;left:0;top:0}
.abs{position:absolute}

/* outside */
.brand{left:18px;top:62px;display:flex;align-items:center;gap:5px;font-family:"Libre Baskerville",Georgia,serif;font-weight:700;font-size:10px;color:var(--blue);width:80px;line-height:1.15}
.brand .dot{width:12px;height:12px;border-radius:50%;background:var(--blue);flex:none}
.wordmark{width:240px;text-align:center;font-family:"Libre Baskerville",Georgia,serif;color:var(--blue)}
.wordmark .name{font-size:29px;line-height:1.05;font-weight:400;letter-spacing:1px}
.wordmark .title{font-size:7px;color:var(--ink);letter-spacing:.5px;margin-top:3px}
.wordmark-left{left:64px;top:80px}
.wordmark-right{left:384px;top:80px}
.lead-note{left:22px;top:192px;width:150px;font-family:"Libre Baskerville",Georgia,serif;font-weight:700;font-size:5.6px;line-height:1.55;color:#3b3f4c}
.caption{left:151px;top:373px;width:190px;color:var(--ink);font-family:"Open Sans",Arial,sans-serif}
.caption .n,.caption .r{font-size:8.4px;line-height:11px}
.caption .d{font-size:5.6px;line-height:8px;margin-top:1px}
.caption .w{font-family:"Crimson Text",Georgia,serif;font-style:italic;font-size:9.4px;line-height:11px;margin-top:4px}
.contact{left:24px;top:458px;color:var(--white);font-family:"Open Sans",Arial,sans-serif;font-size:7.6px}
.contact .who{font-size:10.6px;margin-bottom:5px}
.contact li{list-style:none;display:flex;align-items:center;gap:6px;height:13.5px}
.contact svg{width:9px;height:9px;flex:none}
.badges{left:286px;top:474px;display:flex;gap:8px}
.badges span{width:22px;height:22px;border:1.5px solid rgba(255,255,255,.55)}
.headline{left:376px;top:436px;width:266px;text-align:center;font-family:"Libre Baskerville",Georgia,serif;font-weight:700;font-size:25px;line-height:1.2;color:var(--blue-deep)}

/* inside */
.col{font-size:6.3px;line-height:9.2px;text-align:justify;color:var(--ink-soft)}
.col h2{font-family:"Libre Baskerville",Georgia,serif;font-weight:700;font-size:12px;line-height:18px;color:var(--blue);letter-spacing:.3px;text-align:left;margin-bottom:11px}
.col p{margin-bottom:8px}
.col h2.next{margin-top:18px}
.col-about{left:173px;top:24px;width:166px}
.col-sell{left:377px;top:24px;width:141px}
.col-buy{left:541px;top:24px;width:141px}
.testimonials{left:365px;top:320px;width:326px;text-align:center;color:var(--white);font-size:6.4px;line-height:9.3px}
.testimonials h2{font-family:"Libre Baskerville",Georgia,serif;font-weight:700;font-size:12.5px;letter-spacing:.6px;margin-bottom:8px}
.testimonials p{margin:0}
.testimonials .by{font-family:"Libre Baskerville",Georgia,serif;font-weight:700;font-size:7.4px;margin:2px 0 12px}
</style>
</head>
<body>

<section class="spread spread-outside" aria-label="Folder outside: back and front cover">
  <svg width="709" height="530" viewBox="0 0 709 530">
    <defs>
      <linearGradient id="poolDusk" x1="0" y1="0" x2="1" y2="1">
        <stop offset="0" stop-color="#b9c3dc"/><stop offset=".55" stop-color="#7d8aa8"/><stop offset="1" stop-color="#3e4a67"/>
      </linearGradient>
      <linearGradient id="poolNight" x1="0" y1="0" x2="1" y2="1">
        <stop offset="0" stop-color="#2f4f9c"/><stop offset=".5" stop-color="#6b5b48"/><stop offset="1" stop-color="#2f7fb8"/>
      </linearGradient>
      <linearGradient id="portrait" x1="0" y1="0" x2="0" y2="1">
        <stop offset="0" stop-color="#cdb795"/><stop offset="1" stop-color="#4a4b52"/>
      </linearGradient>
      <clipPath id="frontShape"><path d="M363 0H608Q808 265 608 530H363Z"/></clipPath>
    </defs>
    <!-- back cover -->
    <rect x="0" y="0" width="363" height="530" fill="var(--paper)"/>
    <polygon points="0,176 363,176 363,180 0,200" fill="#9fb2de"/>
    <rect x="0" y="182" width="363" height="186" fill="url(#poolDusk)" role="img" aria-label="Photo of a modern home with a reflecting pool at dusk"/>
    <rect x="4" y="270" width="142" height="210" fill="url(#portrait)" role="img" aria-label="Portrait photo of the agent"/>
    <polygon points="0,478 363,442 363,530 0,530" fill="var(--blue)"/>
    <polygon points="180,460 363,442 363,530 230,530" fill="var(--blue-light)" opacity=".35"/>
    <!-- front cover -->
    <g clip-path="url(#frontShape)">
      <rect x="363" y="0" width="346" height="530" fill="var(--paper-gray)"/>
      <polygon points="363,163 709,180 709,188 363,175" fill="var(--blue)"/>
      <polygon points="363,175 709,188 709,355 363,380" fill="url(#poolNight)" role="img" aria-label="Photo of a luxury home with a lit pool at night"/>
    </g>
  </svg>

  <div class="abs brand"><span class="dot"></span><span>Summit<br>Realty</span></div>
  <div class="abs wordmark wordmark-left"><div class="name">Dana Moretti</div><div class="title">REALTOR</div></div>
  <div class="abs wordmark wordmark-right"><div class="name">Dana Moretti</div><div class="title">REALTOR</div></div>

  <p class="abs lead-note">Along with being your Realtor, I'm a lifelong resource for all things home-related &amp; beyond... If you need a great referral for anything at all, call me! I can't wait to work with you!</p>

  <div class="abs caption">
    <div class="n">Dana Moretti</div>
    <div class="r">Realtor</div>
    <div class="d">DRE# 02481736</div>
    <div class="w">Please feel welcome to call me<br>for all things home related.<br>I will look forward to meeting you!</div>
  </div>

  <div class="abs contact">
    <div class="who">DANA MORETTI</div>
    <ul>
      <li><svg viewBox="0 0 10 10"><circle cx="5" cy="5" r="4.4" fill="none" stroke="#fff" stroke-width=".8"/><path d="M3.3 2.8l1 1-.5.7q.6 1.2 1.7 1.7l.7-.5 1 1-.7.7Q4 7 3 3.5z" fill="#fff"/></svg>555 010 4821</li>
      <li><svg viewBox="0 0 10 10"><circle cx="5" cy="5" r="4.4" fill="none" stroke="#fff" stroke-width=".8"/><rect x="2.8" y="3.4" width="4.4" height="3.2" fill="none" stroke="#fff" stroke-width=".7"/><path d="M2.8 3.4L5 5.2 7.2 3.4" fill="none" stroke="#fff" stroke-width=".6"/></svg>dana@danamhomes.com</li>
      <li><svg viewBox="0 0 10 10"><circle cx="5" cy="5" r="4.4" fill="none" stroke="#fff" stroke-width=".8"/><circle cx="5" cy="5" r="2.4" fill="none" stroke="#fff" stroke-width=".6"/><path d="M2.6 5h4.8" stroke="#fff" stroke-width=".5"/></svg>www.danamhomes.com</li>
    </ul>
  </div>
  <div class="abs badges" aria-hidden="true"><span></span><span></span></div>

  <h1 class="abs headline">We've Got<br>News For You...</h1>
</section>

<section class="spread spread-inside" aria-label="Folder inside pages">
  <svg width="709" height="530" viewBox="0 0 709 530">
    <defs>
      <linearGradient id="villa" x1="0" y1="0" x2="0" y2="1">
        <stop offset="0" stop-color="#5d9be0"/><stop offset=".45" stop-color="#e9e2d6"/><stop offset=".75" stop-color="#6d8a4e"/><stop offset="1" stop-color="#7fb3c9"/>
      </linearGradient>
    </defs>
    <path d="M44 0H166V530H44Q-44 265 44 0Z" fill="url(#villa)" role="img" aria-label="Photo of a Mediterranean-style community entrance with a fountain and palm trees"/>
    <rect x="166" y="0" width="181" height="530" fill="var(--paper)"/>
    <rect x="347" y="0" width="362" height="305" fill="var(--paper-gray)"/>
    <rect x="347" y="305" width="362" height="225" fill="var(--blue)"/>
  </svg>

  <article class="abs col col-about">
    <h2>LET ME INTRODUCE<br>MYSELF</h2>
    <p>I'm originally from Chicago, but I'm a full-fledged California girl now. I've lived and worked in Orange County since 1996. I always say where we live is the next best thing to living on a tropical island. I've traveled to many and I'm always happy to come back to my Laguna Niguel home.</p>
    <p>My passion for this area is why I'm in Real Estate. I consider myself incredibly fortunate to sell homes and help people purchase homes in an area that I love with all my heart.</p>
    <p>This passion also carries over in representing my clients with the highest degree of professionalism, enthusiasm and care. My business is built on exceptional customer service and I'm grateful my clients are mostly repeat and referrals.</p>
    <h2 class="next">MY CORE TENET</h2>
    <p>It's All About YOU!<br>My #1 priority is understanding YOUR needs and YOUR objectives. This understanding, along with working diligently on your behalf, means we accomplish your goal whether you're purchasing your 1st home or selling a home you've loved so you can move on to the next chapter of your life.</p>
    <h2 class="next">REAL ESTATE<br>SERVICES &amp; BEYOND...</h2>
    <p>Simply put, I help people who are local, relocating and investing, sell and purchase homes in Southern California. For purchases outside of California, I can refer to a network of agents across the country.<br>I also provide a team who is dedicated to providing outstanding customer service throughout the transaction. My team includes a network of lenders, title, and escrow officers, in house CPA, stagers, photographers, contractors and more.</p>
  </article>

  <article class="abs col col-sell">
    <h2>SELLING YOUR<br>HOME</h2>
    <p>Selling your home is not like any other business transaction. It's also personal. My priority as your Listing Agent is to guide you through what can be a complicated and sometimes emotional process.</p>
    <p>I place great emphasis on marketing your property with professional photographs, along with harnessing the power of the Internet and the virtual world to reach as many buyers as possible. Your property will be marketed to the public as well as to other agents, thus creating maximum exposure of your home.</p>
    <p>When we first meet to discuss selling your home, it's essential for me to gain an understanding of your unique needs such as timelines, expectations and financial considerations, just to name a few. From there, I begin the process of listing and marketing your home. I lead you through negotiations and more paperwork than you ever care to do, guiding you to the successful closing of your home.</p>
  </article>

  <article class="abs col col-buy">
    <h2>BUYING A<br>HOME</h2>
    <p>If you're thinking about buying a home, it's imperative you have an accomplished, real estate professional by your side to walk you through what is likely the largest purchase of your life.</p>
    <p>To get started, I like to meet with you so we have an opportunity to get to know each other as purchasing a home is a uniquely, personal endeavor. At that time, we can discuss your goals and if it's a good time for you to purchase a home.</p>
    <p>From there, the first step is to obtain a pre-approval from a lender. I'm able to recommend various lenders who can introduce and explain the various loan products available.</p>
    <p>After you've been pre-approved, that's when the fun starts! I guide you through the home buying adventure every step of the way and look forward to handing you the keys to your new home.</p>
  </article>

  <section class="abs testimonials">
    <h2>TESTIMONIALS:</h2>
    <p>Dana got us an amazing deal on our new home and sold our old home in a week. Dana is patient, hardworking, professional and most importantly HONEST. Dana is definitely one of the best in the business!</p>
    <p class="by">Jenna &amp; Mark Ellis</p>
    <p>Dana is the kind of Real Estate professional everyone wants to represent them. She is knowledgeable, ethical, energetic, and follows up on every detail. Her honesty, integrity and expertise combined make her a very special and remarkable professional. We were lucky to find her!</p>
    <p class="by">Paul &amp; Rita Owens</p>
    <p>During the home buying process, Dana becomes your trusted advisor, mentor and friend. Her knowledge of the industry, community and market are best in class. A true professional! Dana aligned her goals with my own and understood the motivation behind my purchase. Dana is unequivocally the reason why I was able to purchase my home in Laguna Niguel and provide my family with a world-class community. Without her guidance and experience, I would still be in the market attempting to navigate the ever-changing work of real estate.</p>
    <p class="by">Luis Serrano</p>
  </section>
</section>

</body>
</html>
```